Logo and Website Design for QR.KA Horizon - a Software Engineering and IT company

Software engineering and IT are two different disciplines - and yet inseparably linked. At QR.KA Horizon, we combine both worlds and ensure that our software solutions are not only innovative and powerful, but also integrate perfectly into existing IT landscapes. Vision stands more for imagination, so it is not neccessary something what has to do with visualisation. Please consider that the winning competitor is also instructed to make a logo for the company. So please make a suitable logo for QR.KA Horizon to which the website fits to and show it during the website creation process. A good Logo desing is important for winning the competition. The website should contain a landing page with inspiring, perhaps futuristic photos of a datacenter and lines of code. Eventuelly flewent integrated in the text. On the landing page the company should introduced with a small text (max 250 words) followed by a section with a short text to one of our products nearby a graphic visualising the architecture of the product. The menue should be on top and fixed during scrolling and consist of the menue items home, solutions, who are we and a contact button. There should be a footer for linking social media, rights and Impressum. Only as an idea not a must. The very first view on the landing page could also be the menue bar and below of it a transparent unsharp photo (e.g. datacenter, lines of code, both ;) with the company name in the center.

###############################################################

Hi Designers,

Despite your very good approaches for describing QR.KA Horizon, here a short introduction (german text) from ourself:

------
QR.KA Horizon – Ihr Partner für ganzheitliche Softwarelösungen

Die QR.KA Horizon ist ein dynamisches Unternehmen, das sich nicht nur auf die Konzeption, das Design und die Entwicklung maßgeschneiderter Software spezialisiert hat, sondern auch deren reibungslosen Betrieb sicherstellt. Mit einem Team aus erfahrenen Softwarearchitekten und IT-Professionals verbinden wir modernste Softwareentwicklung mit tiefgehendem IT-Know-how – für Lösungen, die nachhaltig, leistungsstark und zukunftssicher sind.

Software Engineering trifft IT – Perfektion in Kombination
Software Engineering und IT sind zwei unterschiedliche Disziplinen – und doch untrennbar miteinander verbunden. Wir bei QR.KA Horizon vereinen beide Welten und sorgen dafür, dass unsere Softwarelösungen nicht nur innovativ und leistungsfähig sind, sondern sich auch perfekt in bestehende IT-Landschaften integrieren.

Expertise mit Fokus auf Healthcare & komplexe IT-Umgebungen
Unsere Experten bringen jahrzehntelange Erfahrung aus dem Healthcare-Sektor mit und unterstützen IT-Abteilungen großer Kliniken in der Entwicklung und Optimierung von Softwarelösungen. Von Anwendungssoftware bis hin zu Steuerungssystemen – unsere Softwareingenieure wissen genau, worauf es ankommt.

Ganzheitlicher Ansatz – über die Software hinaus
Wir entwickeln nicht nur Software, sondern übernehmen auch die Verantwortung für deren stabile und effiziente Betriebsumgebung. Egal, ob on-premises, in der Cloud oder als SaaS-Lösung – wir kümmern uns um den kompletten Lifecycle Ihrer Anwendung.

Ihre Vision – unsere Mission.
Ob Neuentwicklung einer SaaS-Anwendung oder die Migration bestehender Lösungen in eine moderne SaaS-Umgebung – mit QR.KA Horizon haben Sie einen starken Partner an Ihrer Seite.

Lassen Sie uns gemeinsam die Zukunft Ihrer Software gestalten!
--------------

Our first solution called "Clear Record Transfer Gateway" (CLURA)
-------------------
Teilen Sie Ihre Daten sicher – ohne Kompromisse!

Sie nutzen eine relationale Datenbank (Brightcask, Tabulon Hub, Vellumdb etc.) und möchten ausgewählte Daten mit Dritten teilen – sei es für ein Data Warehouse, Business Controller, Lieferanten oder Kunden? Doch dabei sollen Datensicherheit, Integrität und Verfügbarkeit Ihrer primären Lösung in keiner Weise gefährdet werden?

Mit unserer Lösung erhalten Sie genau das: Maximalen Schutz für Ihre Anwendung bei gleichzeitigem Nutzen durch autorisierte Dritte – ganz ohne teure Lizenzkosten für eine Schattendatenbank.

Lassen Sie uns gemeinsam herausfinden, wie Sie Ihre Daten sicher und effizient nutzen können. Kontaktieren Sie uns – wir zeigen Ihnen, was möglich ist!
---------------------

Our second solution MIVO:
---------------------
MIVO – Program for a Tone Matching Instrument ist die smarte Lösung für Unternehmen, die bei Farbgenauigkeit keine Kompromisse machen. Die Software erkennt Farbabweichungen zwischen Mustern vollautomatisch, beschreibt sie verständlich und sorgt so für gleichbleibend hohe Produktqualität – schnell, visuell und präzise. Perfekt für alle, die Farbe zur Vertrauenssache machen.
-------------------------

Thanks,
Gerold

Target Market(s)

IT Professionals from any sector

Industry/Entity Type

Healthcare and other

Coding

Coded - Design and coding required

Number of Pages Required

1 page

Font styles to use
Sans Serif

Colors
0054AA
0677BA
7BADD7
CADEEF
E8F1F8
0094D4
00A9DD
6FCCEA
C7EBF8
E9F6FB
00AB8E
00BBA5
67D7C9
C6EFE9
E9F9F6

Requirements
Must have
• Please see description
Nice to have
• On the landing page the company should introduced with a small text (max 250 words) followed by a section with a short text to one of our products nearby a graphic visualising the architecture of the product. The menue should be on top and fixed during scrolling and consist of the menue items home, solutions, who are we and a contact button. There should be a footer for linking social media, rights and Impressum. Only as an idea not a must. The very first view on the landing page could also be the menue bar and below of it a transparent unsharp photo (e.g. datacenter, lines of code, both ;) with the company name in the center.
Should not have
• Please see description

```html
<!DOCTYPE html>
<html lang="de">
<head>
<meta charset="utf-8">
<title>QR.KA Horizon – Softwarelösungen</title>
<link rel="stylesheet" href="https://fonts.googleapis.com/css2?family=Lato:wght@400;700;900&family=Montserrat:wght@800&family=Open+Sans:wght@400;600&display=swap">
<style>
:root{
  --blue-deep:#0054aa;
  --blue:#0677ba;
  --blue-soft:#e8f1f8;
  --teal:#00ab8e;
  --teal-mid:#00bba5;
  --teal-light:#67d7c9;
  --navy:#020a1c;
  --ink:#111111;
  --white:#ffffff;
  --violet:#2b1d7c;
}
*{margin:0;padding:0;box-sizing:border-box}
html,body{width:1200px;height:3033px;overflow:hidden}
body{position:relative;background:var(--white);font-family:"Open Sans",sans-serif;color:var(--ink)}
.abs{position:absolute}

.topbar{left:0;top:0;width:1200px;height:35px;background:var(--blue-soft);font-size:13.5px;color:#222}
.topbar .item{position:absolute;top:8px;display:flex;align-items:center;gap:8px}
.topbar svg{width:20px;height:16px}

.nav{left:0;top:35px;width:1200px;height:76px;background:var(--white)}
.nav a{position:absolute;top:27px;font-size:14px;color:var(--ink);text-decoration:none;font-family:"Open Sans",sans-serif}
.nav a.active{color:var(--teal)}
.brand{font-family:"Lato",sans-serif;font-weight:900;color:var(--blue-deep);letter-spacing:-.3px}
.nav .brand{position:absolute;left:0;width:1200px;text-align:center;top:20px;font-size:34px}

.hero-art{left:0;top:111px;width:1200px;height:570px}
.hero-title{left:0;top:300px;width:1200px;text-align:center;font-family:"Montserrat",sans-serif;font-weight:800;font-size:41px;line-height:51px;color:var(--white)}
.btn{display:inline-block;height:34px;line-height:34px;padding:0 15px;border-radius:17px;background:var(--teal);color:var(--white);font-size:13.5px;font-family:"Open Sans",sans-serif;text-decoration:none}
.btn.dark{background:var(--blue-deep)}
.hero-btn{left:523px;top:424px}

.about-photo{left:139px;top:766px;width:409px;height:412px;background:linear-gradient(160deg,#1b1f66 0%,#3b2a9a 45%,#8a2a66 80%,#2b1450 100%)}
.about-text{left:650px;top:830px;width:410px}
h2.section-h{font-family:"Lato",sans-serif;font-weight:700;font-size:27px;line-height:36px;color:var(--ink)}
h2.section-h .name{color:var(--blue-deep)}
p.body{font-size:12.5px;line-height:24px;color:#222;margin-top:16px}

.products-bg{left:0;top:1178px;width:1200px;height:1080px;background:linear-gradient(180deg,#fff 0%,var(--blue-soft) 14%,var(--blue-soft) 82%,#fff 100%)}
.products-head{left:0;top:1306px;width:1200px;text-align:center}
.products-head h2{font-family:"Lato",sans-serif;font-weight:700;font-size:27px;color:var(--ink)}
.products-head p{font-size:13px;line-height:19px;margin-top:14px;color:#222}

.product h3{font-family:"Lato",sans-serif;font-weight:700;font-size:16.5px;line-height:24px;color:var(--ink)}
.product p{font-size:13px;line-height:23px;color:#222;margin-top:12px}
.product .btn{margin-top:26px}
.prod-one{left:141px;top:1464px;width:410px}
.prod-two{left:650px;top:1913px;width:410px}
.prod-art{background:radial-gradient(circle at 50% 52%,#3a2a9c 0%,#2c1d84 45%,var(--violet) 72%)}
.art-one{left:651px;top:1438px;width:409px;height:412px}
.art-two{left:145px;top:1888px;width:408px;height:412px}

.cta{left:0;top:2398px;width:1200px;height:420px;background:var(--teal-light)}
.cta h2{position:absolute;left:0;top:62px;width:1200px;text-align:center;font-family:"Lato",sans-serif;font-weight:900;font-size:27.5px;line-height:42px;color:#071226}
.cta .btn{position:absolute;left:523px;top:165px}

.footer-shape{left:0;top:2650px;width:1200px;height:335px}
.footer-brand{left:0;top:2808px;width:1200px;text-align:center;font-size:34px}
.footer-brand.brand{color:var(--blue)}
.contact{top:2885px;display:flex;align-items:center;gap:12px;color:var(--white);font-size:13px;line-height:19px}
.contact svg{width:32px;height:34px;flex:none}
.divider{top:2886px;width:1px;height:38px;background:#1d2940}

.bottombar{left:0;top:2982px;width:1200px;height:51px;background:var(--blue-deep);color:var(--white);font-size:12.5px}
.bottombar .copy{position:absolute;left:142px;top:17px}
.socials{position:absolute;right:140px;top:12px;display:flex;gap:9px}
.socials span{width:26px;height:26px;border-radius:50%;background:var(--white);display:block}
</style>
</head>
<body>

<header class="abs topbar">
  <div class="item" style="left:141px">
    <svg viewBox="0 0 20 16"><rect x="1" y="2" width="18" height="12" fill="var(--blue-deep)"/><path d="M1 2l9 7 9-7" fill="none" stroke="#fff" stroke-width="1.4"/></svg>
    info@qrkahorizon.example
  </div>
  <div class="item" style="right:142px">
    <svg viewBox="0 0 20 20"><path d="M5 3l3 4-2 2c1 2 3 4 5 5l2-2 4 3-2 3C9 18 2 11 2 5z" fill="none" stroke="var(--blue-deep)" stroke-width="1.6"/><path d="M12 3a5 5 0 015 5M12 6a2 2 0 012 2" fill="none" stroke="var(--blue-deep)" stroke-width="1.4"/></svg>
    +00 321 654 0987
  </div>
</header>

<nav class="abs nav">
  <a href="#" class="active" style="left:291px">Startseite</a>
  <a href="#" style="left:403px">Lösungen</a>
  <div class="brand">QR.KA Horizon</div>
  <a href="#" style="left:732px">Wer wir sind</a>
  <a href="#" style="left:862px">Kontakt</a>
</nav>

<svg class="abs hero-art" viewBox="0 0 1200 570" role="img" aria-label="Futuristisches Foto mit Codezeilen und leuchtender Datenwelle in Blau und Violett">
  <defs>
    <linearGradient id="heroFill" x1="0" y1="0" x2="0" y2="1">
      <stop offset="0" stop-color="#020714"/>
      <stop offset=".35" stop-color="#0a1f5a"/>
      <stop offset=".7" stop-color="#1c3cb0"/>
      <stop offset=".9" stop-color="#4a2ab5"/>
      <stop offset="1" stop-color="#1b2fa8"/>
    </linearGradient>
    <linearGradient id="arcStroke" x1="0" y1="0" x2="1" y2="0">
      <stop offset="0" stop-color="var(--teal)"/>
      <stop offset=".5" stop-color="var(--teal-light)"/>
      <stop offset="1" stop-color="var(--blue-deep)"/>
    </linearGradient>
  </defs>
  <path d="M0 0H1200V470Q600 590 0 470Z" fill="url(#heroFill)"/>
  <path d="M141 510Q600 600 1059 510Q600 570 141 510Z" fill="url(#arcStroke)"/>
</svg>
<h1 class="abs hero-title">Technik im digitalen Zeitalter<br>Gestaltung von Lösungen durch Software</h1>
<a href="#" class="abs btn hero-btn">Kontaktieren Sie uns</a>

<div class="abs about-photo" role="img" aria-label="Foto eines Arbeitsplatzes mit Monitor voller Codezeilen, Tablet und Tastatur in blauem Licht"></div>
<section class="abs about-text">
  <h2 class="section-h"><span class="name">QR.KA Horizon</span>-Ihr Partner für ganzheitliche Softwarelösungen</h2>
  <p class="body">QR.KA Horizon ist ein dynamisches Unternehmen, das sich nicht nur auf die Konzeption, Gestaltung und Entwicklung von Individualsoftware spezialisiert hat, sondern auch für deren reibungslosen Betrieb sorgt. Mit einem Team aus erfahrenen Softwarearchitekten und IT-Profis verbinden wir modernste Softwareentwicklung mit fundiertem IT-Know-how - für Lösungen, die nachhaltig, leistungsstark und zukunftssicher sind.</p>
</section>

<div class="abs products-bg"></div>
<div class="abs products-head">
  <h2>Ausgewähltes Produkt</h2>
  <p>Lorem ipsum dolor sit amet, consectetuer adipiscing elit, sed diam nonummy nibh euismod<br>tincidunt ut laoreet dolore magna aliquam erat volutpat wisi enim ad minim veniam</p>
</div>

<section class="abs product prod-one">
  <h3>Offene Datenaustauschschnittstelle (CLURA)</h3>
  <p>Sie verwenden eine relationale Datenbank (Brightcask, Tabulon Hub, Vellumdb usw.) und möchten ausgewählte Daten mit Dritten teilen - sei es für ein Data Warehouse, Business Controller, Lieferanten oder Kunden? Sie wollen aber die Datensicherheit, -integrität und -verfügbarkeit Ihrer primären Lösung in keiner Weise gefährden? Mit unserer Lösung erhalten Sie genau das: maximalen Schutz für Ihre Anwendung bei gleichzeitiger Nutzung durch autorisierte Dritte - ohne die teuren Lizenzkosten für eine Schattendatenbank.<br>Lassen Sie uns gemeinsam herausfinden, wie Sie Ihre Daten sicher und effizient nutzen können.</p>
  <a href="#" class="btn">Kontaktieren Sie uns</a>
</section>
<div class="abs prod-art art-one" role="img" aria-label="Isometrische Illustration von Laptops um einen zentralen Datenchip als Architektur der Schnittstelle"></div>

<div class="abs prod-art art-two" role="img" aria-label="Isometrische Illustration eines Laptops mit Lupe zur Prüfung der Farbgenauigkeit"></div>
<section class="abs product prod-two">
  <h3>Software zur Qualitätssicherung der Farbgenauigkeit ( MIVO)</h3>
  <p>MIVO ist die intelligente Lösung für Unternehmen, die bei der Farbgenauigkeit keine Kompromisse eingehen. Die Software erkennt automatisch Farbabweichungen zwischen Mustern, beschreibt sie eindeutig und sorgt so für eine gleichbleibend hohe Produktqualität - schnell, visuell und präzise. Perfekt für alle, die Farbe zur Vertrauenssache machen.</p>
  <a href="#" class="btn">Kontaktieren Sie uns</a>
</section>

<section class="abs cta">
  <h2>Ermutigung der Besucher, sich mit Ihnen in Verbindung zu setzen, um<br>Lösungen für die sichere und effiziente Nutzung ihrer Daten zu finden.</h2>
  <a href="#" class="btn dark">Kontaktieren Sie uns</a>
</section>

<svg class="abs footer-shape" viewBox="0 0 1200 335" aria-hidden="true">
  <path d="M0 108Q600 -30 1200 108V335H0Z" fill="var(--navy)"/>
  <path d="M141 67Q600 -20 1059 67Q600 5 141 67Z" fill="var(--blue-deep)"/>
</svg>
<div class="abs brand footer-brand">QR.KA Horizon</div>

<div class="abs contact" style="left:255px">
  <svg viewBox="0 0 32 34"><path d="M16 4a8 8 0 018 8c0 6-8 14-8 14S8 18 8 12a8 8 0 018-8z" fill="none" stroke="#fff" stroke-width="1.5"/><circle cx="16" cy="12" r="3" fill="none" stroke="#fff" stroke-width="1.5"/><path d="M5 30h22" stroke="#fff" stroke-width="1.5"/></svg>
  <div>45, Lindenhof Lane<br>Brookfield, Region QZ 654321</div>
</div>
<div class="abs divider" style="left:502px"></div>
<div class="abs contact" style="left:545px">
  <svg viewBox="0 0 32 34"><path d="M8 6l5 6-3 3c2 4 5 7 9 9l3-3 6 5-3 4C14 30 4 20 4 10z" fill="none" stroke="#fff" stroke-width="1.5"/><path d="M18 5a9 9 0 019 9M18 10a4 4 0 014 4" fill="none" stroke="#fff" stroke-width="1.4"/></svg>
  <div>TELEFON<br>+00 321 654 0987</div>
</div>
<div class="abs divider" style="left:735px"></div>
<div class="abs contact" style="left:778px">
  <svg viewBox="0 0 32 34"><rect x="3" y="12" width="26" height="18" fill="none" stroke="#fff" stroke-width="1.5"/><path d="M3 12l13 10 13-10M8 16V4h16v12M11 9h10M11 13h10" fill="none" stroke="#fff" stroke-width="1.4"/></svg>
  <div>E-MAIL<br>info@qrkahorizon.example</div>
</div>

<footer class="abs bottombar">
  <div class="copy">© 2025 QR.KA Horizon. All Rights Reserved.</div>
  <div class="socials"><span></span><span></span><span></span><span></span></div>
</footer>

</body>
</html>
```